Website Design for a Luxury Wedding & Events Company

We are launching a British luxury wedding & event planning consultancy business providing bespoke, elegant and first-class service to our discerning clients in the UK and abroad. We specialize in Weddings (which will have it's on page) however we also provide service for other occasion which will be included in a single page 'Events'.

We require a company website design befitting of our luxury brand. Once designed we will post another job to code the website so that it can be hosted by HostPlume.com.

The website has to set the tone for our business and type of premium service we provide. Our website design has to be BESPOKE and have a luxury and elegant look and feel about it.

PLEASE REFER TO THE IMAGES ATTACHED TO GET AN UNDERSTANDING OF THE DESIGN CONCEPT WE WANT. ALL DESIGNS SUBMITTED MUST FOLLOW THE CONCEPT SPECIFIED!!!

We appreciate that the current budget will not permit for the design of all pages referenced above, so we are happy to have designs for up to 3 pages initially; Landing page (we have attached an examples of what we want), 'Home' page (an example is also attached) and 'About' us page. When we are happy with a particular design we can add payment for remainder of the pages required.

The final website design will have the following pages:
1a) URL Landing Page (details below)
1b) Home
2) About
3) Luxury Weddings
4) Services (this can either be a separate tab or linked to 'Luxury Weddings' - however it does need to be a separate page)
subheadings are:
> Comprehensive Wedding Planning Service
> Wedding Day Coordination Service
> Consultancy Service
5) Events
6) Gallery
7) Testimonials
8) Contact

We have a concept of the website is as follows:
URL Landing Page:
Option 1: This should just be simple but makes an immediate statement.
We have attached an image of how this could potentially look. The logo featured in the photo example needs to be replaced with our logo (reference site: http://tesslovank.com/).

Option 2: Alternatively this could be an actually door in the middle of the page - Imagine the big black gloss door at Number 14 Corwell Terrace (London Prime Minister's home).

By clicking the door knocker on either options , the 'Home Page' will be opened.

Our tag line should also be tastefully integrated:
'Exclusive Events, Masterfully Produced, Distinctively Designed'

The 'HOME PAGE' - should look like a luxury boutique office or reception lounge (luxury table, luxury head chair and luxury 2 client chairs; elegant chandelier, beautiful flowers on the table, 2 flutes of champagne on the table; and filing cabinets with drawers that are labelled with different website pages, e.g. 'about us', 'services', 'gallery', etc. By clicking on the drawers the details behind that page will open up in a separate tab/page.)

Our tag line should be on the Home Page also.

The overall concept and look and feel of website is all about taking people on a journey and giving them a glimpse of the luxury service that awaits them.

Colours: We want the general look and feel of the website to be WHITE, or OFF-WHITE with soft hints of gold to match the logo (tab/page headings could be gold). The only dark page should be the URL Landing page (ref to website images attached).

The website and images need to be compatible with mobile devices, smartphones, Tabros, etc. In terms of fit to screen, resolution etc...

We require links to our Pagewall, Quillet, Snapvuely and Boardlyne Pages (links to be provided later)

This is the rough concept and looking for designers to try to elevate this vision. :-) We are open for designers to interpret this concept in their own way.

Website wording/content is all ready to go...

We have attached our logo, and some imagery to help...

Target Market(s)

Luxury Wedding & Events Market

Industry/Entity Type

Wedding Planner

Number of Pages Required

3 page

Font styles to use
Sans Serif

Colors
ffffff

Requirements
Must have
• Tag Line:
• 'Exquisite Events, Masterfully Produced, Distinctively Designed'

```html
<!DOCTYPE html>
<html lang="en">
<head>
<meta charset="utf-8">
<title>Elara Whitcombe – Luxury Weddings &amp; Events</title>
<link rel="stylesheet" href="https://fonts.googleapis.com/css2?family=Alegreya+Sans:wght@400;500;700&family=Open+Sans:wght@400;600&display=swap">
<style>
:root{
  --gold:#b8862f;
  --gold-light:#d9b46a;
  --yellow:#e6d21a;
  --ink:#333333;
  --muted:#666666;
  --dark:#2a2a2a;
  --darker:#232323;
  --blush:#f6eef0;
  --white:#ffffff;
}
*{box-sizing:border-box;margin:0;padding:0}
html,body{width:1200px;height:3930px;overflow:hidden;background:var(--white)}
body{position:relative;font-family:"Open Sans",Arial,sans-serif;color:var(--ink)}
.section{position:absolute;left:0;width:1200px}
.title{position:absolute;left:0;width:100%;text-align:center;font-family:"Alegreya Sans",Arial,sans-serif;font-weight:400;font-size:44px;color:var(--gold)}
.hearts{position:absolute;left:0;width:100%;display:flex;justify-content:center;gap:16px}
.copy{position:absolute;left:80px;width:1040px;text-align:center;font-size:13px;line-height:22px;color:var(--muted)}

/* header */
.site-header{top:0;height:212px;background:var(--dark)}
.brand{position:absolute;top:28px;left:0;width:100%;text-align:center}
.brand-mark{width:80px;height:80px;border:2px solid var(--gold);border-radius:50%;margin:0 auto}
.brand-name{margin-top:8px;font-family:"Alegreya Sans",Arial,sans-serif;font-weight:500;font-size:26px;letter-spacing:3px;color:var(--gold-light);text-transform:uppercase}
.brand-sub{font-size:8px;letter-spacing:2px;color:var(--gold-light);text-transform:uppercase}
.main-nav{position:absolute;top:174px;left:80px;width:1040px;display:flex;justify-content:space-between;font-family:"Alegreya Sans",Arial,sans-serif;font-size:15px;color:var(--gold-light);text-transform:uppercase;letter-spacing:.5px}

/* hero */
.hero{top:212px;height:553px;background:linear-gradient(100deg,#cfc6bd 0%,#e9e2da 35%,#9b8a80 60%,#5b4a45 80%,#3b2e2c 100%)}
.tagline{position:absolute;left:280px;top:378px;width:642px;height:90px;background:rgba(168,124,48,.88);border:1px solid var(--gold-light);color:#fff;font-family:"Alegreya Sans",Arial,sans-serif;font-size:24px;line-height:28px;text-align:center;padding-top:17px;text-transform:uppercase}
.dots{position:absolute;left:0;width:100%;display:flex;justify-content:center;gap:20px}
.dot{width:10px;height:10px;border-radius:50%;border:1px solid #fff}
.dot.on{background:var(--gold);border-color:var(--gold)}

/* luxury */
.luxury{top:1087px;height:336px;background:linear-gradient(180deg,#f8f4f5,var(--blush) 50%,#faf7f8)}
.title .ink{color:var(--ink)}

/* packages */
.package{position:absolute;top:1603px;height:210px;border:2px solid var(--gold-light);padding:8px;background:#fff}
.package-photo{width:100%;height:100%}
.package-name{position:absolute;top:1830px;width:320px;text-align:center;font-family:"Alegreya Sans",Arial,sans-serif;font-weight:700;font-size:21px;color:var(--gold);line-height:24px}
.package-name small{display:block;font-family:"Open Sans",Arial,sans-serif;font-weight:400;font-size:14px;color:var(--ink)}
.subtitle{position:absolute;top:1960px;left:0;width:100%;text-align:center;font-family:"Alegreya Sans",Arial,sans-serif;font-weight:400;font-size:24px;color:var(--gold)}

/* gallery */
.gallery{top:2200px;height:740px;background:linear-gradient(135deg,#b88838,#a5762c 45%,#c0913f 75%,#9e6f27)}
.gallery .title{color:var(--yellow)}
.gallery .title span{color:#fff}
.shot{position:absolute}

/* testimonials */
.avatar{position:absolute;left:527px;top:3121px;width:146px;height:146px;border-radius:50%;border:5px solid var(--yellow);background:linear-gradient(160deg,#f1e5df,#d9c3b9)}
.reviewer{position:absolute;top:3278px;left:0;width:100%;text-align:center;font-family:"Alegreya Sans",Arial,sans-serif;font-size:25px;color:var(--ink)}
.dots.grey .dot{border-color:#bbb}
.dots.grey .dot.on{background:var(--yellow);border-color:var(--yellow)}

/* contact */
.contact{top:3503px;height:427px;background:linear-gradient(180deg,#2d2b2b,var(--darker))}
.contact-intro{position:absolute;top:3645px;left:0;width:100%;text-align:center;font-size:13px;color:#fff}
.contact-line{position:absolute;top:3690px;display:flex;align-items:center;gap:12px;font-size:23px;color:#fff}
.socials{position:absolute;top:3787px;left:0;width:100%;display:flex;justify-content:center;gap:22px}
.social{width:56px;height:56px;border:2px solid var(--yellow);border-radius:50%;display:flex;align-items:center;justify-content:center;font-size:9px;color:var(--yellow)}
.copyright{position:absolute;top:3896px;left:0;width:100%;text-align:center;font-size:10px;color:#ccc}
</style>
</head>
<body>

<header class="section site-header">
  <div class="brand">
    <div class="brand-mark"></div>
    <div class="brand-name">Elara Whitcombe</div>
    <div class="brand-sub">Luxury Wedding &amp; Event Consultancy</div>
  </div>
  <nav class="main-nav">
    <span>Home</span><span>About</span><span>Luxury Weddings</span><span>Services</span><span>Events</span><span>Gallery</span><span>Testimonials</span><span>Contact</span>
  </nav>
</header>

<section class="section hero" role="img" aria-label="Bride and groom about to kiss among falling rose petals beside a white balustrade">
  <div class="tagline">“Exclusive Events, Masterfully Produced,<br>Distinctively Designed”</div>
  <div class="dots" style="top:518px"><i class="dot"></i><i class="dot"></i><i class="dot on"></i><i class="dot"></i><i class="dot"></i></div>
</section>

<section class="section about" style="top:765px;height:322px">
  <h2 class="title" style="top:60px">About Us</h2>
  <div class="hearts" style="top:122px"><svg width="14" height="12" viewBox="0 0 14 12"><path d="M7 11 L1.5 5.5 A3 3 0 0 1 7 2 A3 3 0 0 1 12.5 5.5 Z" fill="none" stroke="#d9b46a"/></svg><svg width="14" height="12" viewBox="0 0 14 12"><path d="M7 11 L1.5 5.5 A3 3 0 0 1 7 2 A3 3 0 0 1 12.5 5.5 Z" fill="#b8862f"/></svg></div>
  <p class="copy" style="top:158px">Elara Whitcombe is a British luxury wedding and event planning consultancy providing bespoke, elegant and first class service to our discerning clients in the UK and abroad. Our specialist team of event planning consultants will help elevate your vision and create impeccable designs for life's most important occasions with refinement and tasteful restraint. For us merely satisfying expectations is not enough, we aim to always surpass them.</p>
</section>

<section class="section luxury">
  <h2 class="title" style="top:80px">Luxury <span class="ink">Weddings</span></h2>
  <div class="hearts" style="top:142px"><svg width="14" height="12" viewBox="0 0 14 12"><path d="M7 11 L1.5 5.5 A3 3 0 0 1 7 2 A3 3 0 0 1 12.5 5.5 Z" fill="none" stroke="#d9b46a"/></svg><svg width="14" height="12" viewBox="0 0 14 12"><path d="M7 11 L1.5 5.5 A3 3 0 0 1 7 2 A3 3 0 0 1 12.5 5.5 Z" fill="#b8862f"/></svg></div>
  <p class="copy" style="top:180px">The difference between an ordinary and extraordinary wedding is all in the detail. Each Elara Whitcombe wedding seeks to indulge each of the 5 senses: sound, smell, sight, touch and taste, contributing to an experience that is tastefully executed to subtly create a memorable and lasting impression. From small and intimate to large and lavish affairs in the UK or abroad, Elara Whitcombe wedding consultants ensure that each wedding is perfectly tailored to every couple's discerning taste and budget.</p>
</section>

<section class="section packages" style="top:0;height:0">
  <h2 class="title" style="top:1497px">Packages <span class="ink">&amp;</span> Services</h2>
  <div class="hearts" style="top:1562px"><svg width="14" height="12" viewBox="0 0 14 12"><path d="M7 11 L1.5 5.5 A3 3 0 0 1 7 2 A3 3 0 0 1 12.5 5.5 Z" fill="none" stroke="#d9b46a"/></svg><svg width="14" height="12" viewBox="0 0 14 12"><path d="M7 11 L1.5 5.5 A3 3 0 0 1 7 2 A3 3 0 0 1 12.5 5.5 Z" fill="#b8862f"/></svg></div>
  <div class="package" style="left:86px;width:315px"><div class="package-photo" role="img" aria-label="Outdoor wedding aisle with white chairs and a floral arch" style="background:linear-gradient(180deg,#cfe3ef,#e9eee6 45%,#7ea04a 75%,#5c7f32)"></div></div>
  <div class="package" style="left:440px;width:320px"><div class="package-photo" role="img" aria-label="Bridesmaids in purple dresses holding bouquets" style="background:linear-gradient(135deg,#3a2c66,#5b3f8c 50%,#e9dde0 80%,#c9d47a)"></div></div>
  <div class="package" style="left:791px;width:322px"><div class="package-photo" role="img" aria-label="Reception chairs dressed with pink sashes" style="background:linear-gradient(135deg,#f3e8ee,#d7a6bf 50%,#a34d7e 80%,#f4eef0)"></div></div>
  <div class="package-name" style="left:83px">Comprehensive<small>Wedding Planning</small></div>
  <div class="package-name" style="left:440px">Wedding Day<small>Coordination</small></div>
  <div class="package-name" style="left:792px">Consultancy<small>Service</small></div>
  <h3 class="subtitle">Other Special Events</h3>
  <p class="copy" style="top:2010px">Although we specialise in wedding planning, we are also able to help you plan your bridal shower, baby shower, christening, luxury parties including milestone birthdays or other special event.</p>
  <p class="copy" style="top:2086px">From event concept design, event styling, production, floral design, catering, set building, lighting, pyrotechnics, sound and sourcing entertainment, our seasoned team will ensure element of the event will leave you and your guests suitably impressed. We apply all the same principles, attention to detail and business practices whatever the event.</p>
</section>

<section class="section gallery">
  <h2 class="title" style="top:70px">Photo <span>Gallery</span></h2>
  <div class="hearts" style="top:132px"><svg width="14" height="12" viewBox="0 0 14 12"><path d="M7 11 L1.5 5.5 A3 3 0 0 1 7 2 A3 3 0 0 1 12.5 5.5 Z" fill="none" stroke="#fff"/></svg><svg width="14" height="12" viewBox="0 0 14 12"><path d="M7 11 L1.5 5.5 A3 3 0 0 1 7 2 A3 3 0 0 1 12.5 5.5 Z" fill="#fff"/></svg></div>
  <div class="shot" role="img" aria-label="Couple walking along a seaside promenade" style="left:81px;top:176px;width:322px;height:225px;background:linear-gradient(135deg,#7fa7c9,#d9cbb4 50%,#3a3a40)"></div>
  <div class="shot" role="img" aria-label="Bridesmaids holding colourful bouquets" style="left:81px;top:415px;width:322px;height:225px;background:linear-gradient(135deg,#3b2b6b,#6a4aa0 50%,#e6a43c 75%,#3e2c6a)"></div>
  <div class="shot" role="img" aria-label="Couple holding hands beside glasses of wine" style="left:417px;top:176px;width:366px;height:178px;background:linear-gradient(135deg,#f2ece6,#d7b39a 50%,#8a2433 80%,#f4efea)"></div>
  <div class="shot" role="img" aria-label="Bride and groom beside a white balustrade" style="left:417px;top:367px;width:366px;height:273px;background:linear-gradient(100deg,#d8d0c8,#ece6df 40%,#8d7d76 70%,#4a3b38)"></div>
  <div class="shot" role="img" aria-label="Pink rose bridal bouquet" style="left:796px;top:176px;width:320px;height:225px;background:radial-gradient(circle at 50% 45%,#e07ab0,#f1d6e4 55%,#f5f2f3)"></div>
  <div class="shot" role="img" aria-label="Elegant reception table with pink centrepiece" style="left:796px;top:415px;width:320px;height:225px;background:linear-gradient(180deg,#ece9ee,#d98aa8 45%,#f4f1f2 70%,#dcd8dc)"></div>
</section>

<section class="section testimonials" style="top:0;height:0">
  <h2 class="title" style="top:3010px">Testimonials</h2>
  <div class="hearts" style="top:3075px"><svg width="14" height="12" viewBox="0 0 14 12"><path d="M7 11 L1.5 5.5 A3 3 0 0 1 7 2 A3 3 0 0 1 12.5 5.5 Z" fill="none" stroke="#d9b46a"/></svg><svg width="14" height="12" viewBox="0 0 14 12"><path d="M7 11 L1.5 5.5 A3 3 0 0 1 7 2 A3 3 0 0 1 12.5 5.5 Z" fill="#b8862f"/></svg></div>
  <div class="avatar" role="img" aria-label="Portrait of the client"></div>
  <div class="reviewer">Harriet, <span style="color:var(--muted)">July 23rd, 2015</span></div>
  <p class="copy" style="top:3330px;left:200px;width:800px">Lorem ipsum dolor sit amet, consectetur adipiscing elit. Vivamus tristique bibendum ex, quis pulvinar dolor rutrum eget. Nunc at ante sit amet sapien pretium euismod at in dolor. Ut scelerisque ultricies ultrices. Nullam vitae libero sed mi commodo commodo nec tempor quam. Vivamus finibus sed lacus dignissim condimentum.</p>
  <div class="dots grey" style="top:3427px"><i class="dot"></i><i class="dot"></i><i class="dot on"></i><i class="dot"></i><i class="dot"></i></div>
</section>

<footer class="section contact">
  <h2 class="title" style="top:58px">Contact</h2>
</footer>
<p class="contact-intro">Thank you for your interest! Please contact us directly. We look forward to working with you! If you'd like to make an appointments</p>
<div class="contact-line" style="left:228px">
  <svg width="22" height="16" viewBox="0 0 22 16"><rect width="22" height="16" rx="1" fill="#e6d21a"/><path d="M1 1 L11 9 L21 1" fill="none" stroke="#232323" stroke-width="1.6"/></svg>
  <span>info@elarawhitcombe.com</span>
</div>
<div class="contact-line" style="left:580px">
  <svg width="22" height="22" viewBox="0 0 22 22"><circle cx="11" cy="11" r="10" fill="#e6d21a"/><path d="M1 11 H21 M11 1 C6 6 6 16 11 21 C16 16 16 6 11 1" fill="none" stroke="#232323" stroke-width="1.2"/></svg>
  <span>www.weddingsbyelarawhitcombe.com</span>
</div>
<div class="socials">
  <span class="social">Quillet</span><span class="social">Pagewall</span><span class="social">Snapvuely</span><span class="social">Boardlyne</span>
</div>
<p class="copyright">EW © 2015 Copyrights. All Rights Reserved.</p>

</body>
</html>
```